Career Development Skills | Business Card & Logo Design

We are looking for a business card including logo design for a new Sydney based business called 'Bright Pathwork'.
We offer a range of services that focus on building the Employability or Employment skills for individuals focusing on job seekers and those interested in building skills required to develop their career. Employability skills are required not only to gain employment, but also to progress within an organisation so as to achieve one's potential.
Updates
Target Market(s)
Our client targets include corporates and govt agencies looking to build skills within their current employee base or assist staff in the transition between roles or workplaces.
Industry/Entity Type
Business
Look and feel
Each slider illustrates characteristics of the customer's brand and the style your logo design should communicate.

```html
<!DOCTYPE html>
<html lang="en">
<head>
<meta charset="utf-8">
<title>Bright Pathwork — Business Cards</title>
<link href="https://fonts.googleapis.com/css2?family=Cinzel:wght@700&family=Dosis:wght@500;600&display=swap" rel="stylesheet">
<style>
  :root{
    --stage:#1b1b1b;
    --card-dark-a:#161616;
    --card-dark-b:#3c3c3c;
    --card-light-a:#d6d6d6;
    --card-light-b:#f7f7f7;
    --teal:#1fa2a6;
    --teal-soft:#2aa8ad;
    --silver:#c9c9c9;
    --rule:#8a8a8a;
    --ink-grey:#7a7a7a;
  }
  *{margin:0;padding:0;box-sizing:border-box}
  html,body{width:1200px;height:1164px;overflow:hidden;background:var(--stage)}
  .canvas{position:relative;width:1200px;height:1164px}

  .card{position:absolute;overflow:hidden}
  .card--front{
    left:110px;top:89px;width:730px;height:444px;
    background:linear-gradient(200deg,var(--card-dark-b) 0%,var(--card-dark-a) 70%);
  }
  .card--back{
    left:405px;top:588px;width:723px;height:442px;
    background:linear-gradient(110deg,var(--card-light-a) 0%,var(--card-light-b) 100%);
  }

  /* front */
  .brand-lockup{
    position:absolute;left:0;right:0;top:175px;
    display:flex;align-items:center;justify-content:center;gap:12px;
  }
  .brand-lockup__dot{width:26px;height:26px;border-radius:50%;background:var(--silver)}
  .brand-lockup__name{
    font-family:'Cinzel',serif;font-weight:700;font-size:22px;color:var(--silver);
  }
  .front-rule{
    position:absolute;left:159px;top:262px;width:424px;height:2px;
    background:linear-gradient(90deg,transparent,var(--rule) 20%,var(--rule) 80%,transparent);
  }
  .front-title{
    position:absolute;left:0;right:0;top:270px;text-align:center;
    font-family:'Cinzel',serif;font-weight:700;font-size:33px;letter-spacing:1px;
    color:var(--teal);
  }

  /* back */
  .contact-rule{position:absolute;left:157px;top:100px;width:2px;height:250px;background:var(--teal-soft)}
  .contact{
    position:absolute;left:186px;
    font-family:'Dosis',sans-serif;font-weight:500;font-size:18px;line-height:21px;
  }
  .contact--primary{top:96px;color:var(--teal-soft)}
  .contact--address{top:185px;color:var(--ink-grey)}
  .contact--phones{top:307px;color:var(--teal-soft)}
  .contact--phones span{color:var(--ink-grey)}
  .back-mark{
    position:absolute;left:575px;top:40px;width:150px;height:150px;border-radius:50%;
    background:radial-gradient(circle at 35% 30%,#e6e6e6,#8f8f8f);
  }
</style>
</head>
<body>
<main class="canvas">
  <section class="card card--front" aria-label="Card front">
    <div class="brand-lockup">
      <span class="brand-lockup__dot"></span>
      <span class="brand-lockup__name">Bright Pathwork</span>
    </div>
    <div class="front-rule"></div>
    <h1 class="front-title">BRIGHT PATHWORK</h1>
  </section>

  <section class="card card--back" aria-label="Card back">
    <div class="contact-rule"></div>
    <p class="contact contact--primary">
      Daniel Harrow - Director<br>
      Brightpathwork.com.au<br>
      Daniel@brightpathwork.com.au
    </p>
    <p class="contact contact--address">
      Level 14<br>
      Harbourview Tower 3<br>
      88&nbsp;&nbsp;&nbsp;Kent Lane<br>
      Harbourview, Sydney 2000
    </p>
    <p class="contact contact--phones">
      Tell --------------- <span>(02)&nbsp; 55501234</span><br>
      Fax --------------- <span>(02)&nbsp; 55501299</span>
    </p>
    <div class="back-mark"></div>
  </section>
</main>
</body>
</html>
```